1 Page for Computer Repair Website

Looking for a 1 page website with a design that compliments the business card and pamphlet that have already been made (attached files). It should look business professional and easy to read. Email and phone number should be somewhere near the top of the website, visible when the page loads. I don't want any forms for people to mess with. No "Contact Us" form or entering in email for newsletter. Customers will just be looking at this site to confirm we are professionals and have our business in order.

Target Market(s)

Home and small business

Industry/Entity Type

Computer Repair

Coding

Coded - Design and coding required

Number of Pages Required

1 page

Font styles to use
Other font styles liked:
• Helvetica variations used in pamphlet and card

Colors
0455a3
cfdeed
85abd2
3276b5
85cae6
ffffff

Requirements
Must have
• Compliment the pamphlet and business card in color choices and font use. Pleasing to the eye and easy to read through categories and text.
Should not have
• Forms. No "enter name and email here" or anything of the sort.

```html
<!DOCTYPE html>
<html lang="en">
<head>
<meta charset="utf-8">
<title>NexaFix Computer Services</title>
<link rel="stylesheet" href="https://fonts.googleapis.com/css2?family=Arimo:wght@400;700&display=swap">
<style>
:root{
  --navy:#0455a3;
  --pale:#cfdeed;
  --sky:#85abd2;
  --mid:#3276b5;
  --aqua:#85cae6;
  --white:#ffffff;
  --ink:#1d2b3a;
  --body:#4a5563;
  --band:#e9f1f8;
  --dark:#2a2d31;
  --darker:#1f2225;
}
*{box-sizing:border-box;margin:0;padding:0}
html,body{width:1200px;height:4164px;overflow:hidden}
body{font-family:"Arimo",Helvetica,Arial,sans-serif;color:var(--body);background:var(--white);position:relative}
.block{position:absolute;left:0;width:1200px}

/* hero */
.hero{top:0;height:760px;background:linear-gradient(180deg,#f4f7fa 0%,#eef3f8 70%,#d4e6f3 100%);overflow:hidden}
.hero-photo{position:absolute;right:0;top:0;width:640px;height:760px;background:linear-gradient(135deg,#f3f6fa 0%,#c9dcec 45%,#8fb3d3 75%,#5d8fbf 100%)}
.hero-band{position:absolute;left:0;bottom:0;width:1200px;height:200px;background:linear-gradient(180deg,rgba(133,202,230,0) 0%,rgba(133,202,230,.55) 100%)}
.brand{position:absolute;left:36px;top:28px}
.brand-name{font-size:46px;font-weight:400;color:var(--ink);letter-spacing:1px;line-height:1}
.brand-sub{font-size:15px;color:var(--mid);margin-top:4px;letter-spacing:.5px}
.nav{position:absolute;left:420px;top:38px;display:flex;gap:40px;font-size:17px;color:var(--ink)}
.nav .active{color:var(--navy)}
.contact{position:absolute;left:56px;top:262px;color:var(--navy)}
.contact .lead{font-size:46px;line-height:1.1}
.contact .phone,.contact .email{font-size:66px;line-height:1.15;margin-top:10px}
.chevron{position:absolute;left:574px;top:732px;width:52px;height:52px;border-radius:50%;background:var(--white);border:2px solid var(--sky);z-index:3;display:flex;align-items:center;justify-content:center}

/* about */
.about{top:760px;height:380px;background:linear-gradient(180deg,#a9d3ec 0%,#b9dcef 100%);text-align:center;padding-top:70px}
.about h2{font-size:32px;font-weight:400;color:var(--navy);margin-bottom:24px}
.about p{width:800px;margin:0 auto 18px;font-size:15px;line-height:1.55;color:#2f5f8c}

/* services */
.service{height:285px}
.service.tint{background:var(--band)}
.service .art{position:absolute;top:32px;width:420px;height:220px;border-radius:6px}
.service .copy{position:absolute;top:80px;width:540px}
.service.art-left .art{left:120px}
.service.art-left .copy{left:600px}
.service.art-right .art{right:110px}
.service.art-right .copy{left:110px}
.service h3{font-size:34px;font-weight:400;color:var(--ink);margin-bottom:18px;white-space:nowrap}
.service h3 span{color:var(--navy)}
.service p{font-size:15px;line-height:1.6}

/* why */
.why{top:3420px;height:420px;background:linear-gradient(180deg,#2e3a46 0%,#1c2530 100%);text-align:center}
.why h2{font-size:30px;font-weight:400;color:var(--white);padding-top:28px}
.why-line{position:absolute;left:140px;top:238px;width:920px;height:6px;background:var(--mid)}
.why-node{position:absolute;top:200px;width:80px;height:80px;border-radius:50%;background:var(--navy);border:6px solid var(--white);display:flex;align-items:center;justify-content:center}
.why-node.alt{background:var(--sky)}
.why-text{position:absolute;width:170px;font-size:14px;line-height:1.45;color:#d7e3ee;text-align:left}

/* footer */
.footer{top:3840px;height:324px;background:var(--dark)}
.foot-nav{position:absolute;left:80px;top:36px;display:flex;gap:18px}
.foot-nav span{font-size:14px;color:var(--white);padding:8px 20px;border-radius:20px}
.foot-nav .active{border:1px solid var(--white)}
.social{position:absolute;right:80px;top:30px;display:flex;gap:16px}
.social i{display:block;width:42px;height:42px;border-radius:50%;border:2px solid #9aa3ad}
.foot-rule{position:absolute;left:80px;top:100px;width:1040px;height:1px;background:#4a4f55}
.foot-brand{position:absolute;left:80px;top:136px}
.foot-brand .brand-name{color:var(--white)}
.foot-brand .brand-sub{color:var(--sky)}
.foot-info{position:absolute;top:150px;display:flex;align-items:center;gap:10px;font-size:15px;color:#c9d1d9}
.copyright{position:absolute;left:0;top:240px;width:1200px;text-align:center;font-size:13px;color:#8d959e}
.top-btn{position:absolute;right:40px;top:256px;width:44px;height:44px;border-radius:50%;background:#44494f;display:flex;align-items:center;justify-content:center}
</style>
</head>
<body>

<header class="block hero">
  <div class="hero-photo" role="img" aria-label="Photo of a businessman holding a tablet against a bright city skyline"></div>
  <div class="hero-band"></div>
  <div class="brand">
    <div class="brand-name">NexaFix</div>
    <div class="brand-sub">Computer Services</div>
  </div>
  <nav class="nav">
    <span class="active">Home</span><span>About Us</span><span>Services</span><span>Contact Us</span>
  </nav>
  <div class="contact">
    <div class="lead">Call Us When You Need Us</div>
    <div class="phone">555-014-2290</div>
    <div class="email">help@nexafix.net</div>
  </div>
</header>

<div class="chevron">
  <svg width="22" height="14" viewBox="0 0 22 14"><path d="M2 2l9 9 9-9" fill="none" stroke="#3276b5" stroke-width="3"/></svg>
</div>

<section class="block about">
  <h2>About Us</h2>
  <p>We are a local team of certified technicians who repair, upgrade and maintain computers for homes and small businesses. Every job is quoted up front, explained in plain language and backed by our workmanship guarantee on parts and labour.</p>
  <p>Since opening our doors we have helped thousands of neighbours get back online quickly. Whether it is a slow laptop, a failed drive or a new office network, we treat your equipment and your data with care.</p>
</section>

<section class="block service art-left" style="top:1140px">
  <div class="art" role="img" aria-label="Photo of a man sitting cross-legged working on a laptop" style="background:linear-gradient(135deg,#eef2f6,#b8c4d0)"></div>
  <div class="copy">
    <h3><span>Honest</span> Service</h3>
    <p>Our certified technicians work on honest terms. No pressure to upgrade and no parts you do not need. Every part eventually wears out, and when yours does we will tell you plainly what makes sense.</p>
  </div>
</section>

<section class="block service tint art-right" style="top:1425px">
  <div class="art" role="img" aria-label="Illustration of a red prohibition sign over a virus" style="background:linear-gradient(135deg,#f3e4e4,#d04a4a)"></div>
  <div class="copy">
    <h3>Malware/Virus <span>Removal</span></h3>
    <p>Infections can come from many places and sometimes without you even noticing. We clean your system, restore top speed and set up protection so it stays safe in the future.</p>
  </div>
</section>

<section class="block service art-left" style="top:1710px">
  <div class="art" role="img" aria-label="Photo of a desktop computer, laptops and a keyboard" style="background:linear-gradient(135deg,#f2f4f6,#9fb2c4)"></div>
  <div class="copy">
    <h3>PC/Laptop <span>Hardware</span> Repair</h3>
    <p>Find out exactly which part of your computer is failing and causing trouble. Our technicians will find the best value replacement and install it quickly, on site or in our shop.</p>
  </div>
</section>

<section class="block service tint art-right" style="top:1995px">
  <div class="art" role="img" aria-label="Photo of a hand holding a stopwatch beside a speed gauge" style="background:linear-gradient(135deg,#e9eef3,#7d93a8)"></div>
  <div class="copy">
    <h3>Upgrades</h3>
    <p>A new video card to play the latest game at the highest settings? A new disk to give your laptop a fresh start? We source the parts and make the upgrade hassle-free.</p>
  </div>
</section>

<section class="block service art-left" style="top:2280px">
  <div class="art" role="img" aria-label="Illustration of folders moving to a monitor with a red first-aid cross" style="background:linear-gradient(135deg,#f6efd2,#8cc3e0)"></div>
  <div class="copy">
    <h3>Data <span>Migration &amp; Rescue</span></h3>
    <p>We can make your new computer feel like your old friend. Transfer all your files, photos, bookmarks and settings. Drive crashed? We recover as much as possible from failing or damaged media.</p>
  </div>
</section>

<section class="block service tint art-right" style="top:2565px">
  <div class="art" role="img" aria-label="Illustration of a laptop with crossed wrench and screwdriver" style="background:linear-gradient(135deg,#d7e4f1,#3a5f86)"></div>
  <div class="copy">
    <h3>Tune Ups</h3>
    <p>Over time, systems can get bogged down by unnecessary files and programs running in the background. We clean up startup items, update drivers and get your computer running at peak performance.</p>
  </div>
</section>

<section class="block service art-left" style="top:2850px">
  <div class="art" role="img" aria-label="Illustration of a house with a computer, printer and network cables" style="background:linear-gradient(135deg,#eef4ea,#7fa36a)"></div>
  <div class="copy">
    <h3>In-Home <span>Installation</span></h3>
    <p>All our services come with pick-up and drop-off installation. You won't be left to set up wireless networking, printers, updates or controllers on your own.</p>
  </div>
</section>

<section class="block service tint art-right" style="top:3135px">
  <div class="art" role="img" aria-label="Illustration of two monitors connected for remote support" style="background:linear-gradient(135deg,#dfe8f0,#2f3d4c)"></div>
  <div class="copy">
    <h3>Remote <span>Support</span></h3>
    <p>Small problems shouldn't cost an arm and a leg to fix. We'll set up remote support to your computer to efficiently and cost-effectively solve what can be solved without a technician visit.</p>
  </div>
</section>

<section class="block why">
  <h2>Why Choose Us</h2>
  <div class="why-line"></div>

  <div class="why-text" style="left:110px;top:96px">Certified technicians with years of hands-on repair experience.</div>
  <div class="why-text" style="left:280px;top:306px">Clear, upfront pricing with no hidden fees.</div>
  <div class="why-text" style="left:450px;top:96px">Fast turnaround on most repairs and upgrades.</div>
  <div class="why-text" style="left:620px;top:306px">On-site visits for homes and small offices.</div>
  <div class="why-text" style="left:790px;top:96px">Your files and privacy are always protected.</div>
  <div class="why-text" style="left:960px;top:306px">Friendly local support before and after service.</div>

  <div class="why-node" style="left:128px"><svg width="30" height="30" viewBox="0 0 30 30"><path d="M6 16l6 6 12-13" fill="none" stroke="#fff" stroke-width="3.5"/></svg></div>
  <div class="why-node alt" style="left:298px"><svg width="30" height="30" viewBox="0 0 30 30"><rect x="5" y="7" width="20" height="16" rx="2" fill="none" stroke="#fff" stroke-width="3"/></svg></div>
  <div class="why-node" style="left:468px"><svg width="30" height="30" viewBox="0 0 30 30"><circle cx="15" cy="15" r="10" fill="none" stroke="#fff" stroke-width="3"/><path d="M15 9v6l4 3" fill="none" stroke="#fff" stroke-width="3"/></svg></div>
  <div class="why-node alt" style="left:638px"><svg width="30" height="30" viewBox="0 0 30 30"><path d="M5 15l10-9 10 9v10H5z" fill="none" stroke="#fff" stroke-width="3"/></svg></div>
  <div class="why-node" style="left:808px"><svg width="30" height="30" viewBox="0 0 30 30"><rect x="7" y="13" width="16" height="12" rx="2" fill="none" stroke="#fff" stroke-width="3"/><path d="M10 13V9a5 5 0 0 1 10 0v4" fill="none" stroke="#fff" stroke-width="3"/></svg></div>
  <div class="why-node alt" style="left:978px"><svg width="30" height="30" viewBox="0 0 30 30"><path d="M9 5l4 4-3 4c2 4 4 6 8 8l3-3 4 4-3 3C13 25 5 17 6 8z" fill="#fff"/></svg></div>
</section>

<footer class="block footer">
  <div class="foot-nav">
    <span class="active">HOME</span><span>SERVICE</span><span>ABOUT US</span><span>CONTACT US</span>
  </div>
  <div class="social"><i></i><i></i><i></i></div>
  <div class="foot-rule"></div>
  <div class="foot-brand">
    <div class="brand-name">NexaFix</div>
    <div class="brand-sub">Computer Services</div>
  </div>
  <div class="foot-info" style="left:470px">
    <svg width="18" height="18" viewBox="0 0 30 30"><path d="M9 5l4 4-3 4c2 4 4 6 8 8l3-3 4 4-3 3C13 25 5 17 6 8z" fill="#85abd2"/></svg>
    555-014-2290
  </div>
  <div class="foot-info" style="left:820px">
    <svg width="20" height="16" viewBox="0 0 20 16"><rect x="1" y="1" width="18" height="14" rx="1" fill="none" stroke="#85abd2" stroke-width="2"/><path d="M1 2l9 7 9-7" fill="none" stroke="#85abd2" stroke-width="2"/></svg>
    help@nexafix.net
  </div>
  <div class="copyright">© 2024 NexaFix. All Rights Reserved.</div>
  <div class="top-btn"><svg width="18" height="12" viewBox="0 0 18 12"><path d="M2 10l7-7 7 7" fill="none" stroke="#fff" stroke-width="2.5"/></svg></div>
</footer>

</body>
</html>
```